RIVERSTONE PULSE GYM FLYER DESIGN

We want a flyer designed for our gym. We have an example of a flyer which we like and I have put it into the images I have uploaded. I would like to recreate using our pictures, so its a pretty straight forward job. We also want to put our weekly timetable on the back of the flyer. We would like the size of the flyer to be A5.

Target Market(s)

FITNESS

Industry/Entity Type

Gym

Colors
33a6d7
ffffff

Requirements
Must have
• We just want to recreate the flyer but we must have the following info on the flyer and we want our timetable on the back of the flyer which you can get from this link: http://www.riverstonepulsegym-example.com/timetable
• Riverstone Pulse Gym is a fun community of humble people. Our goal is to help guide you towards a fitter, healthier lifestyle!
• Our Programs
• HIIT
• High intensity interval training is 30-45 minutes of fat burning fun. The class is a mix of cardio, bodyweight and some resistance movements.
• Conditioning
• A full hour of strength, cardio and bodyweight training to get you in tip top shape. Expect a mix of barbells, kettlebells, rowing machines, bikes and other training methods.
• BWS
• This is our big Friday session to set you up for the weekend. 90 minutes of hard training that is done with a team emphasis. From heavy lifting to cardio triathlons, this class has it all but not for the faint hearted.
• Muay Thai
• Commonly known as the science of 8 limbs you will learn how to punch, kick, knee and elbow. Thailands national sport is a great way to get your fitness kick. We train the complete beginner all the way to international fighters so you are in great hands.
• Kids Muay Thai
• Our junior program starts from age 6 onwards. Muay Thai is a great way for kids to get active and fit while learning new skills. Training in martial arts also teaches self discipline and socialisation skills.
• Yoga
• A combination of physical and mental practises that will leave you focused and refreshed for whatever the week throws at you. We always recommend our yoga classes as a great way to balance the high intensity training we offer.
• Q-Press
• Strength training with a little bit of conditioning. We regularly update the program and re test lifts to ensure you are making progress and getting stronger.
• CONTACT US
• OUR LOCATION:
• Unit 27C
• 214 Kelvane Road
• Marrow Heath
• Glasgow
• G72QT
• Phone: 07930625184
• Email: info@riverstonepulsegym-example.com
• Web: www.riverstonepulsegym-example.com
Nice to have
• Can use all the picture but if not be good to use the boxing one and the group training one.

```html
<!DOCTYPE html>
<html lang="en">
<head>
<meta charset="utf-8">
<title>Riverstone Pulse Gym – Flyer</title>
<link href="https://fonts.googleapis.com/css2?family=Oswald:wght@200;300;400;500;700&family=Open+Sans:wght@400;600&display=swap" rel="stylesheet">
<style>
:root{
  --brand:#33a6d7;
  --white:#ffffff;
  --stage:#e9eef1;
  --row-alt:#d5e9f6;
  --line:#b9d7ec;
  --ink-dark:#1d4f69;
  --pink:#cf78b6;
  --rust:#b5622c;
  --olive:#6b7a3a;
  --teal:#2f6d7a;
  --red:#c3252d;
  --purple:#7b3f98;
  --choc:#5b3a22;
  --orange:#e0782a;
  --kids-light:#cfe6f5;
  --kids-blue:#2a7fc1;
  --navy:#17394a;
  --green:#3cb44b;
  --photo-dark:#23414f;
  --photo-warm:#8a5a4a;
}
*{box-sizing:border-box;margin:0;padding:0}
html,body{width:1200px;height:928px;overflow:hidden;background:var(--stage)}
.flyer-page{
  position:absolute;top:67px;width:588px;height:835px;
  background:var(--brand);color:var(--white);overflow:hidden;
  transform:scale(.95);transform-origin:top left;
  font-family:"Open Sans",sans-serif;
}
.flyer-front{left:30px}
.flyer-back{left:611px}

/* FRONT */
.front-shapes{position:absolute;inset:0;width:588px;height:835px}
.tagline{
  position:absolute;left:22px;top:32px;width:175px;
  font-family:"Oswald",sans-serif;font-weight:200;font-size:20px;line-height:27px;
}
.tagline .quote-mark{font-weight:700;font-size:30px;line-height:20px;vertical-align:-6px;margin-right:2px}
.programs{position:absolute;left:230px;top:290px;width:325px}
.programs h2{
  font-family:"Oswald",sans-serif;font-weight:500;font-size:36px;letter-spacing:.5px;
  margin-left:22px;margin-bottom:12px;line-height:44px;
}
.program{position:relative;padding-left:25px;margin-bottom:8px}
.program::before{
  content:"";position:absolute;left:0;top:3px;width:12px;height:12px;border-radius:50%;
  background:var(--white);box-shadow:inset 0 0 0 3px var(--white),inset 0 0 0 6px var(--brand);
}
.program h3{font-family:"Oswald",sans-serif;font-weight:300;font-size:14px;line-height:17px;text-transform:uppercase}
.program p{font-size:9.2px;line-height:11.6px;text-align:justify;opacity:.92}
.contact-front{position:absolute;left:22px;top:556px;width:190px;color:var(--brand);font-family:"Oswald",sans-serif}
.brand-mark{display:flex;align-items:center;gap:7px;font-family:"Oswald",sans-serif;font-weight:500;font-size:15px;letter-spacing:.5px;color:var(--brand)}
.brand-mark .square{width:12px;height:12px;background:var(--brand);flex:none}
.contact-front .brand-mark{margin-bottom:42px}
.contact-front h4{font-weight:400;font-size:12.5px;line-height:16px}
.contact-front p{font-weight:300;font-size:12px;line-height:17px}
.contact-front p.small{font-size:10.5px}
.contact-front .label{font-weight:400;font-size:12px}
.contact-front .gap{margin-top:6px}

/* BACK */
.back-hero{position:absolute;left:0;top:0;width:250px;height:200px;background:radial-gradient(ellipse at 35% 30%,rgba(255,255,255,.22),rgba(255,255,255,0) 70%)}
.tt-title{position:absolute;left:0;right:0;top:22px;text-align:center;font-family:"Oswald",sans-serif;font-weight:700;font-size:42px;line-height:50px;letter-spacing:.5px}
.tt-sub{position:absolute;left:0;right:0;top:73px;text-align:center;font-size:10.5px}
.timetable{
  position:absolute;left:38px;top:95px;width:510px;height:627px;background:var(--white);
  font-family:"Oswald",sans-serif;color:var(--ink-dark);
}
.tt-rows{position:absolute;left:0;right:0;top:15px;bottom:0;
  background:repeating-linear-gradient(180deg,var(--white) 0 16.1px,var(--row-alt) 16.1px 32.2px);
}
.tt-cols{position:absolute;left:46px;right:0;top:0;bottom:0;
  background:repeating-linear-gradient(90deg,var(--line) 0 1px,transparent 1px 66.3px);
}
.tt-days{position:absolute;left:46px;top:0;right:0;height:15px;display:flex}
.tt-days span{width:66.3px;text-align:center;font-size:9.5px;line-height:15px}
.tt-time{position:absolute;left:0;width:46px;text-align:center;font-size:9.5px;line-height:16px;top:calc(15px + (var(--h) - 5) * 32.2px)}
/* --d: 1 = Monday … 6 = Saturday (0 = Sunday) */
.ev{
  position:absolute;display:flex;align-items:center;justify-content:center;text-align:center;
  left:calc(46px + (var(--d) + 1 + var(--x,0)) * 66.3px + 1px);
  width:calc(var(--w,1) * 66.3px - 2px);
  top:calc(15px + (var(--s) - 5) * 32.2px + 1px);
  height:calc((var(--e) - var(--s)) * 32.2px - 2px);
  color:var(--white);font-weight:300;font-size:9.5px;line-height:9.5px;border-radius:2px;
}
.ev.tiny{font-size:5.5px;line-height:6px}
.ev.vert span{transform:rotate(-90deg);white-space:nowrap}
.pink{background:var(--pink)}.rust{background:var(--rust)}.olive{background:var(--olive)}
.teal{background:var(--teal)}.red{background:var(--red)}.purple{background:var(--purple)}
.choc{background:var(--choc)}.orange{background:var(--orange)}.navy{background:var(--navy)}
.kids-light{background:var(--kids-light);color:var(--kids-blue)}
.kids-blue{background:var(--kids-blue)}.green{background:var(--green)}
.back-footer{position:absolute;left:42px;top:748px;right:20px;font-family:"Oswald",sans-serif;font-weight:300;font-size:12px;line-height:17px}
.back-footer .brand-mark{position:absolute;left:0;top:14px;width:110px;color:var(--white);font-size:13px;line-height:16px}
.back-footer .brand-mark .square{background:var(--white)}
.back-footer .location{position:absolute;left:132px;top:0}
.back-footer .reach{position:absolute;left:318px;top:8px;line-height:24px}
.back-footer b{font-weight:400}
</style>
</head>
<body>

<section class="flyer-page flyer-front">
  <svg class="front-shapes" viewBox="0 0 588 835">
    <polygon points="227,0 588,0 588,250 187,278" fill="var(--photo-warm)" role="img" aria-label="Photo: coach holding pads for a boxer in the ring"/>
    <polygon points="0,311 187,282 187,410 0,440" fill="var(--photo-dark)" role="img" aria-label="Photo: athlete training with a medicine ball"/>
    <polygon points="0,440 187,410 187,446 0,581" fill="#2e5566" role="img" aria-label="Photo: group training class on the gym floor"/>
    <polygon points="0,581 187,446 220,835 0,835" fill="var(--white)"/>
  </svg>

  <p class="tagline"><span class="quote-mark">“</span>Riverstone Pulse Gym is a fun community of humble people. Our goal is to help guide you towards a fitter, healthier lifestyle!</p>

  <div class="programs">
    <h2>OUR PROGRAMS</h2>
    <div class="program"><h3>HIIT</h3><p>High intensity interval training is 30-45 minutes of fat burning fun. The class is a mix of cardio, bodyweight and some resistance movements.</p></div>
    <div class="program"><h3>Conditioning</h3><p>A full hour of strength, cardio and bodyweight training to get you in tip top shape. Expect a mix of barbells, kettlebells, rowing machines, bikes and other training methods.</p></div>
    <div class="program"><h3>BWS</h3><p>This is our big Friday session to set you up for the weekend. 90 minutes of hard training that is done with a team emphasis. From heavy lifting to cardio triathlons, this class has it all but not for the faint hearted.</p></div>
    <div class="program"><h3>Muay Thai</h3><p>Commonly known as the science of 8 limbs you will learn how to punch, kick, knee and elbow. Thailands national sport is a great way to get your fitness kick. We train the complete beginner all the way to international fighters so you are in great hands.</p></div>
    <div class="program"><h3>Kids Muay Thai</h3><p>Our junior program starts from age 6 onwards. Muay Thai is a great way for kids to get active and fit while learning new skills. Training in martial arts also teaches self discipline and socialisation skills.</p></div>
    <div class="program"><h3>Yoga</h3><p>A combination of physical and mental practises that will leave you focused and refreshed for whatever the week throws at you. We always recommend our yoga classes as a great way to balance the high intensity training we offer.</p></div>
    <div class="program"><h3>Q-Press</h3><p>Strength training with a little bit of conditioning. We regularly update the program and re test lifts to ensure you are making progress and getting stronger.</p></div>
  </div>

  <div class="contact-front">
    <div class="brand-mark"><span class="square"></span>RIVERSTONE PULSE GYM</div>
    <h4>OUR LOCATION:</h4>
    <p>Unit 27C<br>214 Kelvane Road, Marrow Heath<br>Glasgow G72QT</p>
    <p class="gap"><span class="label">Phone:</span> 07930625184</p>
    <p class="gap small"><span class="label">Email:</span> info@riverstonepulsegym-example.com</p>
    <p class="gap small"><span class="label">Web:</span> www.riverstonepulsegym-example.com</p>
  </div>
</section>

<section class="flyer-page flyer-back">
  <div class="back-hero" role="img" aria-label="Faded photo of an athlete in motion"></div>
  <h1 class="tt-title">TIMETABLE</h1>
  <p class="tt-sub">See below for our full timetable of classes please see our Website for more info and class descriptions</p>

  <div class="timetable">
    <div class="tt-rows"></div>
    <div class="tt-cols"></div>
    <div class="tt-days"><span>SUN</span><span>MON</span><span>TUE</span><span>WED</span><span>THU</span><span>FRI</span><span>SAT</span></div>

    <div class="tt-time" style="--h:5">5 AM</div>
    <div class="tt-time" style="--h:6">6 AM</div>
    <div class="tt-time" style="--h:7">7 AM</div>
    <div class="tt-time" style="--h:8">8 AM</div>
    <div class="tt-time" style="--h:9">9 AM</div>
    <div class="tt-time" style="--h:10">10 AM</div>
    <div class="tt-time" style="--h:11">11 AM</div>
    <div class="tt-time" style="--h:12">12 PM</div>
    <div class="tt-time" style="--h:13">1 PM</div>
    <div class="tt-time" style="--h:14">2 PM</div>
    <div class="tt-time" style="--h:15">3 PM</div>
    <div class="tt-time" style="--h:16">4 PM</div>
    <div class="tt-time" style="--h:17">5 PM</div>
    <div class="tt-time" style="--h:18">6 PM</div>
    <div class="tt-time" style="--h:19">7 PM</div>
    <div class="tt-time" style="--h:20">8 PM</div>
    <div class="tt-time" style="--h:21">9 PM</div>
    <div class="tt-time" style="--h:22">10 PM</div>
    <div class="tt-time" style="--h:23">11 PM</div>

    <div class="ev pink" style="--d:1;--s:6;--e:7">Q-Press</div>
    <div class="ev rust" style="--d:2;--s:6;--e:7">Strength &amp;<br>Conditioning</div>
    <div class="ev pink" style="--d:4;--s:6;--e:7">Q-Press</div>
    <div class="ev olive" style="--d:0;--s:7;--e:8">Conditioning</div>
    <div class="ev teal" style="--d:1;--s:7;--e:8">Fight Camp<br>Muay Thai</div>
    <div class="ev red" style="--d:2;--s:7;--e:8">Yoga [5/25]</div>
    <div class="ev olive" style="--d:3;--s:7;--e:8">Conditioning</div>
    <div class="ev teal" style="--d:4;--s:7;--e:8">Fight Camp<br>Muay Thai</div>
    <div class="ev purple" style="--d:0;--s:8;--e:10">Open Gym</div>
    <div class="ev purple" style="--d:1;--s:8;--e:10">Open Gym</div>
    <div class="ev purple" style="--d:2;--s:8;--e:10">Open Gym</div>
    <div class="ev purple" style="--d:3;--s:8;--e:10">Open Gym</div>
    <div class="ev purple" style="--d:4;--s:8;--e:10">Open Gym</div>
    <div class="ev pink" style="--d:0;--s:10;--e:11">Q-Press</div>
    <div class="ev pink" style="--d:2;--s:10;--e:11">Q-Press</div>
    <div class="ev pink" style="--d:4;--s:10;--e:11">Q-Press</div>
    <div class="ev choc" style="--d:5;--s:10;--e:11">Saturday Circuit</div>
    <div class="ev purple vert" style="--d:5;--x:0;--w:.25;--s:11;--e:12.75"><span>Open Gym</span></div>
    <div class="ev kids-blue tiny vert" style="--d:5;--x:.25;--w:.25;--s:11;--e:12"><span>Kids</span></div>
    <div class="ev purple" style="--d:5;--x:.25;--w:.25;--s:12;--e:12.75"></div>
    <div class="ev kids-light tiny" style="--d:5;--x:.5;--w:.5;--s:11;--e:12">Kids</div>
    <div class="ev teal tiny" style="--d:5;--x:.5;--w:.5;--s:12;--e:12.75">Muay Thai<br>Foundation</div>
    <div class="ev orange tiny" style="--d:0;--s:12.125;--e:12.55">LUNCH TIME HIIT</div>
    <div class="ev orange tiny" style="--d:1;--s:12.125;--e:12.55">LUNCH TIME HIIT</div>
    <div class="ev orange tiny" style="--d:3;--s:12.125;--e:12.55">LUNCH TIME HIIT</div>
    <div class="ev orange tiny" style="--d:4;--s:12.125;--e:12.55">LUNCH TIME HIIT</div>

    <div class="ev purple" style="--d:0;--s:16;--e:17">Open Gym</div>
    <div class="ev pink" style="--d:0;--w:.5;--s:17;--e:18">Q-Press</div>
    <div class="ev pink" style="--d:0;--w:.15;--s:18;--e:19"></div>
    <div class="ev kids-blue tiny vert" style="--d:0;--x:.17;--w:.3;--s:18;--e:19"><span>Kids</span></div>
    <div class="ev teal tiny" style="--d:0;--x:.5;--w:.5;--s:18;--e:19">Muay Thai<br>Foundation</div>
    <div class="ev rust" style="--d:0;--s:19;--e:20">Strength &amp;<br>Conditioning</div>

    <div class="ev purple" style="--d:1;--w:.5;--s:16;--e:18">Open<br>Gym</div>
    <div class="ev orange tiny" style="--d:1;--x:.5;--w:.5;--s:17;--e:17.7">HIIT<br>[13/30]</div>
    <div class="ev olive tiny" style="--d:1;--w:.5;--s:18;--e:19">Conditioning</div>
    <div class="ev kids-light tiny" style="--d:1;--x:.5;--w:.5;--s:18;--e:19">Kids</div>
    <div class="ev navy" style="--d:1;--s:19;--e:20">Muay Thai<br>Intermediate</div>

    <div class="ev purple" style="--d:2;--s:16;--e:17">Open Gym</div>
    <div class="ev pink" style="--d:2;--w:.5;--s:17;--e:18">Q-Press</div>
    <div class="ev orange tiny" style="--d:2;--x:.5;--w:.5;--s:17;--e:17.7">HIIT<br>[13/30]</div>
    <div class="ev pink" style="--d:2;--w:.15;--s:18;--e:19"></div>
    <div class="ev kids-blue tiny vert" style="--d:2;--x:.17;--w:.3;--s:18;--e:19"><span>Kids</span></div>
    <div class="ev teal tiny" style="--d:2;--x:.5;--w:.5;--s:18;--e:19">Muay Thai<br>Foundation</div>
    <div class="ev red" style="--d:2;--s:19.25;--e:20.25">Yoga [5/25]</div>

    <div class="ev purple" style="--d:3;--w:.5;--s:16;--e:18">Open<br>Gym</div>
    <div class="ev orange tiny" style="--d:3;--x:.5;--w:.5;--s:17;--e:17.7">HIIT<br>[13/30]</div>
    <div class="ev olive tiny" style="--d:3;--w:.5;--s:18;--e:19">Conditioning</div>
    <div class="ev kids-light tiny" style="--d:3;--x:.5;--w:.5;--s:18;--e:19">Kids</div>
    <div class="ev navy" style="--d:3;--s:19;--e:20">Muay Thai<br>Intermediate</div>

    <div class="ev purple" style="--d:4;--s:16;--e:17">Open Gym</div>
    <div class="ev pink" style="--d:4;--w:.5;--s:17;--e:18">Q-Press</div>
    <div class="ev green tiny" style="--d:4;--x:.5;--w:.5;--s:18;--e:19.4">BWS</div>
  </div>

  <div class="back-footer">
    <div class="brand-mark"><span class="square"></span>RIVERSTONE PULSE GYM</div>
    <div class="location"><b>OUR LOCATION:</b><br>Unit 27C<br>214 Kelvane Road, Marrow Heath<br>Glasgow G72QT</div>
    <div class="reach"><b>Phone:</b> 07930625184<br><b>Email:</b> info@riverstonepulsegym-example.com<br><b>Web:</b> www.riverstonepulsegym-example.com</div>
  </div>
</section>

</body>
</html>
```